Business Card for Professional Photographer

I'm looking for an eye catching modern clean design that compliments my logo/ website fonts & colours.
I specialise in architecture, corporate & commercial photography so I'm marketing to professional clients rather than portrait / wedding clients.

I would prefer to not have a solid black design.

My logo brand guide is as follows :

Main front font. : Reislust
Main font colour : #fff
Slogan front font : Ubuntu Bold
Monogram front font : Venti Medium
Container colour : #fff

I need print ready files in pdf .png & .eps formats.

Included in the files below are some screen grabs as reference to font & colours etc.

```html
<!DOCTYPE html>
<html lang="en">
<head>
<meta charset="utf-8">
<title>Northline Studio – Business Card</title>
<link href="https://fonts.googleapis.com/css2?family=Montserrat:wght@400;500;600&display=swap" rel="stylesheet">
<style>
  :root {
    --bg: #5a5a5c;
    --card: #ffffff;
    --ink: #4a4a4a;
    --ink-soft: #6a6a6a;
    --gold: #c9973f;
    --gold-light: #f6e3a0;
    --gold-dark: #b8862f;
    --slate: #4b4b4d;
    --sky: #a9c3e3;
    --pavement: #9a9a9a;
    --icon: #222222;
  }
  * { margin: 0; padding: 0; box-sizing: border-box; }
  html, body { width: 1200px; height: 960px; overflow: hidden; }
  body {
    background: var(--bg);
    font-family: "Montserrat", sans-serif;
    color: var(--ink);
    position: relative;
  }
  .card {
    position: absolute;
    left: 250px;
    width: 700px;
    height: 400px;
    border-radius: 22px;
    overflow: hidden;
    background: var(--card);
    box-shadow: 0 10px 30px rgba(0,0,0,0.35);
  }
  .card--front { top: 50px; }
  .card--back { top: 510px; }

  /* Front */
  .front-photo {
    position: absolute; inset: 0;
    background: linear-gradient(180deg, var(--sky) 0%, #d8e2ee 35%, #e8e4dc 55%, var(--pavement) 78%, #8f8f8f 100%);
  }
  .front-veil { position: absolute; inset: 0; background: rgba(255,255,255,0.45); }
  .brand {
    position: absolute;
    display: flex; align-items: center; gap: 14px;
  }
  .brand__mark {
    width: 22px; height: 22px;
    border: 3px solid var(--gold);
    border-radius: 3px;
    flex: none;
  }
  .brand__name {
    font-weight: 400;
    letter-spacing: 0.12em;
    color: var(--ink);
    line-height: 1;
  }
  .brand__tagline {
    font-weight: 600;
    font-size: 9px;
    letter-spacing: 0.18em;
    color: var(--ink-soft);
    margin-top: 5px;
  }
  .card--front .brand { left: 190px; top: 172px; }
  .card--front .brand__name { font-size: 30px; }

  /* Back */
  .side-band { position: absolute; left: 95px; width: 95px; }
  .side-band--slate { top: 0; height: 95px; background: var(--slate); }
  .side-band--gold {
    top: 160px; bottom: 0;
    background: linear-gradient(180deg, var(--gold-dark) 0%, var(--gold-light) 35%, #e7c477 65%, var(--gold) 100%);
  }
  .icon-column { position: absolute; left: 95px; width: 95px; top: 160px; bottom: 0; }
  .icon-column svg { position: absolute; left: 39px; width: 16px; height: 16px; fill: var(--icon); }
  .card--back .brand { left: 115px; top: 100px; }
  .card--back .brand__name { font-size: 24px; }
  .card--back .brand__mark { width: 44px; height: 44px; background: var(--card); }

  .contact {
    position: absolute; left: 225px; top: 170px;
    font-size: 15px; line-height: 1.3; color: var(--ink);
  }
  .contact__name { color: var(--gold); font-weight: 500; font-size: 19px; letter-spacing: 0.02em; }
  .contact__role { font-size: 16px; margin-bottom: 12px; }
  .contact__group { margin-bottom: 12px; }
</style>
</head>
<body>

<section class="card card--front">
  <div class="front-photo" role="img" aria-label="Photograph of a modern white and orange commercial building beside a parking lot under a cloudy blue sky"></div>
  <div class="front-veil"></div>
  <div class="brand">
    <span class="brand__mark"></span>
    <div>
      <div class="brand__name">NORTHLINE STUDIO</div>
      <div class="brand__tagline">Buildings business brand imagery</div>
    </div>
  </div>
</section>

<section class="card card--back">
  <div class="side-band side-band--slate"></div>
  <div class="side-band side-band--gold"></div>

  <div class="brand">
    <span class="brand__mark"></span>
    <div>
      <div class="brand__name">NORTHLINE STUDIO</div>
      <div class="brand__tagline">Buildings business brand imagery</div>
    </div>
  </div>

  <div class="icon-column">
    <svg style="top:14px" viewBox="0 0 20 20" aria-hidden="true"><circle cx="10" cy="6" r="4"/><path d="M2 19c0-5 3.5-7 8-7s8 2 8 7z"/></svg>
    <svg style="top:72px" viewBox="0 0 20 20" aria-hidden="true"><path d="M10 1a6 6 0 0 0-6 6c0 5 6 12 6 12s6-7 6-12a6 6 0 0 0-6-6zm0 8.5A2.5 2.5 0 1 1 10 4.5a2.5 2.5 0 0 1 0 5z"/></svg>
    <svg style="top:121px" viewBox="0 0 20 20" aria-hidden="true"><path d="M5 2l3 4-2 2a11 11 0 0 0 6 6l2-2 4 3-2 3C9 18 2 11 2 4z"/></svg>
    <svg style="top:140px" viewBox="0 0 20 20" aria-hidden="true"><rect x="6" y="1" width="8" height="18" rx="2"/></svg>
    <svg style="top:160px" viewBox="0 0 20 20" aria-hidden="true"><rect x="2" y="8" width="16" height="10" rx="1"/><rect x="5" y="2" width="10" height="5"/></svg>
    <svg style="top:179px" viewBox="0 0 20 20" aria-hidden="true"><path d="M2 4h16v12H2z M2 4l8 7 8-7" stroke="#f3dc98" stroke-width="1.2"/></svg>
    <svg style="top:199px" viewBox="0 0 20 20" aria-hidden="true"><circle cx="10" cy="10" r="8"/></svg>
  </div>

  <div class="contact">
    <div class="contact__name">DANIEL REYES</div>
    <div class="contact__role">President</div>
    <div class="contact__group">214 Harbor View Road<br>Seward, Alaska 99664</div>
    <div>555-014-2281<br>555-019-7340<br>555-016-4492<br>info@northlinestudio.com<br>www.northlinestudio.com</div>
  </div>
</section>

</body>
</html>
```